New letter head for Air Conditioning business

We need a new professional letter head design to suit our new re-branded air conditioning business. Our new logo is attached

```html
<!DOCTYPE html>
<html lang="en">
<head>
<meta charset="utf-8">
<title>Norvent Letterhead</title>
<link href="https://fonts.googleapis.com/css2?family=Open+Sans:wght@400;600;700&family=Kristi&display=swap" rel="stylesheet">
<style>
  :root {
    --backdrop: #e9e9e9;
    --paper: #ffffff;
    --ink: #3a3a3a;
    --ink-soft: #5b5b5b;
    --brand-red: #ef6a5c;
    --brand-green: #3fae6a;
    --brand-dark: #2f3b45;
  }
  * { box-sizing: border-box; margin: 0; padding: 0; }
  html, body {
    width: 1200px; height: 795px; overflow: hidden;
    background: var(--backdrop);
    font-family: "Open Sans", sans-serif;
    color: var(--ink);
  }
  .letterhead {
    position: absolute; left: 340px; top: 30px;
    width: 520px; height: 735px;
    background: var(--paper);
    box-shadow: 0 4px 18px rgba(0,0,0,0.12);
    overflow: hidden;
  }
  .contact-list {
    position: absolute; top: 34px; right: 44px;
    list-style: none; font-size: 7.5px; line-height: 11px; color: var(--ink-soft);
  }
  .contact-list li { display: flex; align-items: center; gap: 5px; }
  .contact-dot {
    width: 7px; height: 7px; border-radius: 50%;
    background: var(--brand-green); flex: none;
  }
  .contact-dot.is-red { background: var(--brand-red); }
  .brand {
    position: absolute; top: 96px; left: 44px;
    display: flex; align-items: center; gap: 7px;
  }
  .brand-dot { width: 14px; height: 14px; border-radius: 50%; background: var(--brand-green); }
  .brand-name {
    font-size: 21px; font-weight: 600; letter-spacing: 3px; color: var(--brand-dark);
  }
  .brand-tagline {
    position: absolute; top: 124px; left: 65px;
    font-size: 5px; letter-spacing: 1px; text-transform: uppercase; color: var(--brand-green);
  }
  .letter {
    position: absolute; top: 178px; left: 44px; width: 420px;
    font-size: 8px; line-height: 11px;
  }
  .letter-date { margin-bottom: 14px; }
  .recipient { margin-bottom: 10px; }
  .salutation { font-weight: 700; font-size: 9px; margin-bottom: 12px; }
  .letter-body p { margin-bottom: 11px; color: var(--ink-soft); }
  .sign-off {
    position: absolute; top: 536px; right: 58px;
    font-size: 8px; line-height: 10px; text-align: left; width: 120px;
  }
  .sign-off .closing { margin-bottom: 2px; }
  .signature {
    font-family: "Kristi", cursive; font-size: 26px; line-height: 26px; color: #222;
  }
  .footer-band { position: absolute; left: 0; bottom: 0; width: 520px; height: 120px; }
  .footer-address {
    position: absolute; right: 24px; bottom: 12px;
    display: flex; align-items: center; gap: 5px;
    font-size: 8px; color: #fff;
  }
  .footer-address .mark { width: 7px; height: 7px; border-radius: 50%; background: #fff; }
  .footer-address strong { font-weight: 700; letter-spacing: 1px; }
</style>
</head>
<body>
  <article class="letterhead">
    <ul class="contact-list">
      <li><span class="contact-dot"></span>(555) 014-2231</li>
      <li><span class="contact-dot is-red"></span>(555) 014-2298</li>
      <li><span class="contact-dot"></span>info@norventair.com</li>
      <li><span class="contact-dot is-red"></span>www.norventair.com</li>
    </ul>

    <div class="brand">
      <span class="brand-dot"></span>
      <span class="brand-name">NORVENT</span>
    </div>
    <div class="brand-tagline">Air Conditioning &amp; Refrigeration</div>

    <section class="letter">
      <p class="letter-date">January 03, 2017</p>
      <p class="recipient">Mr. John Doe<br>President<br>AA Corporation<br>111 Street Name, Suite#<br>City, State, 12345</p>
      <p class="salutation">Dear Mr. John,</p>
      <div class="letter-body">
        <p>Lorem Ipsum is simply dummy text of the printing and typesetting industry. Lorem Ipsum has been the industry's standard dummy text ever since the 1500s, when an unknown printer took a galley of type and scrambled it to make a type specimen book. It has survived not only five centuries, but also the leap into electronic typesetting, remaining essentially unchanged.</p>
        <p>The standard chunk of Lorem Ipsum used since the 1500s is reproduced below for those interested. Sections 1.10.32 and 1.10.33 from "de Finibus Bonorum et Malorum" by Cicero are also reproduced in their exact original form, accompanied by English versions from the 1914 translation by H. Rackham</p>
        <p>Lorem Ipsum is simply dummy text of the printing and typesetting industry. Lorem Ipsum has been the industry's standard dummy text ever since the 1500s, when an unknown printer took a galley of type and scrambled it to make a type specimen book. It has survived not only five centuries, but also the leap into electronic typesetting, remaining essentially unchanged. It was popularised in the</p>
      </div>
    </section>

    <div class="sign-off">
      <p class="closing">Sincerely Your,</p>
      <p class="signature">your name</p>
      <p>Name Last Name<br>Company Name</p>
    </div>

    <svg class="footer-band" viewBox="0 0 520 120" preserveAspectRatio="none">
      <path d="M0,114 C170,104 370,66 520,14" fill="none" stroke="var(--brand-green)" stroke-width="3"/>
      <path d="M0,120 C180,112 380,74 520,24 L520,120 Z" fill="var(--brand-red)"/>
    </svg>
    <p class="footer-address"><span class="mark"></span><strong>NORVENT</strong> : Suite 102 Street name, State, Zip 2034, Country</p>
  </article>
</body>
</html>
```